Business Card for Polygraph business in Africa

Business Card . Polygraph Examiner based in Tanzania, East Africa.
Business Card will be used to disseminate contact information to potential clients.
It should convey that I am a professional specifically in the polygraph field and perform my work with integrity.

I have attached the business card that I'm currently using, which I threw together myself initially. It's not professional enough.

Target Market(s)

Banks, Accounting Firms, Government Ministries, Gas, Oil, & Gemstone Mining Concerns, Wildlife Conservation NGOs, International companies located in East Africa.

Industry/Entity Type

Business

Contact Information for Business Card

Veritrace Kilonga
Miriam Holloway
PO Box 48317
Arusha, Tanzania
+255 612 839 274
miriamholloway@postvale.example

Colors
00a990
f37122
faa54b

Requirements
Must have
• - Veritrace Kilonga (with the word "Polygraph" being more prominent than the word "Tanzania")
• - Forensic Examinations
• - Employment Screening
• - Should contain a logo of the Continental Truthline Society (of which I'm a member)
• - I would like an accent design (such as the polygraph "squiggles" of a cardio tracing or such as that)
• - My contact information (less prominent, but large enough to read legibly). I would also consider putting the contact information on the second side of the card.
Nice to have
• My color suggestions are changeable.
Should not have
• Anything "cutesy" or "cartoonish"

```html
<!DOCTYPE html>
<html lang="en">
<head>
<meta charset="utf-8">
<title>Veritrace Kilonga — Business Card</title>
<link rel="stylesheet" href="https://fonts.googleapis.com/css2?family=Roboto:wght@400;500;700&display=swap">
<style>
  :root {
    --page-bg: #e9e6e1;
    --card-dark: #6a6a6a;
    --card-light: #f5f5f5;
    --brand-blue: #1a4fa8;
    --text-light: #ffffff;
    --text-soft: #eeeeee;
    --rule: #9a9a9a;
    --tagline: #555555;
    --accent-dot: #1a4fa8;
  }
  * { box-sizing: border-box; margin: 0; padding: 0; }
  html, body { width: 1200px; height: 911px; overflow: hidden; }
  body {
    background: var(--page-bg);
    font-family: "Roboto", Arial, sans-serif;
    display: flex;
    align-items: center;
    justify-content: center;
    gap: 80px;
  }
  .card {
    width: 370px;
    height: 648px;
    border-radius: 26px;
    position: relative;
    box-shadow: 0 12px 30px rgba(0,0,0,0.18);
  }
  .card-back { background: var(--card-dark); color: var(--text-light); }
  .card-front { background: var(--card-light); }

  .back-mark {
    position: absolute;
    top: 70px;
    left: 50%;
    transform: translateX(-50%);
    width: 64px;
    height: 64px;
    border: 3px solid var(--text-light);
    border-radius: 50%;
  }
  .contact-block {
    position: absolute;
    left: 42px;
    right: 42px;
    top: 330px;
  }
  .person-name {
    color: var(--brand-blue);
    font-weight: 700;
    font-size: 19px;
    letter-spacing: 0.5px;
    text-transform: uppercase;
  }
  .company-name {
    font-weight: 500;
    font-size: 15px;
    letter-spacing: 0.6px;
    text-transform: uppercase;
    margin-top: 4px;
  }
  .rule { border: none; border-top: 1px solid var(--rule); margin: 16px 0; }
  .address { font-size: 14px; color: var(--text-soft); }
  .contact-list { list-style: none; font-size: 14px; color: var(--text-soft); line-height: 1.55; }
  .contact-list .label { color: var(--brand-blue); font-weight: 700; margin-right: 4px; }

  .brand {
    position: absolute;
    top: 290px;
    left: 0;
    right: 0;
    display: flex;
    align-items: center;
    justify-content: center;
    gap: 12px;
  }
  .brand-circle {
    width: 40px;
    height: 40px;
    border: 3px solid var(--brand-blue);
    border-radius: 50%;
    flex: none;
  }
  .brand-name {
    color: var(--brand-blue);
    font-weight: 700;
    font-size: 30px;
    letter-spacing: 0.2px;
  }
  .tagline {
    position: absolute;
    bottom: 44px;
    left: 0;
    right: 0;
    text-align: center;
    font-size: 13px;
    color: var(--tagline);
  }
  .tagline .dot { color: var(--accent-dot); margin: 0 6px; }
</style>
</head>
<body>
  <section class="card card-back" aria-label="Card back with contact details">
    <div class="back-mark"></div>
    <div class="contact-block">
      <p class="person-name">Miriam Holloway</p>
      <p class="company-name">Veritrace Kilonga</p>
      <hr class="rule">
      <p class="address">PO Box 48317, Arusha, Tanzania</p>
      <hr class="rule">
      <ul class="contact-list">
        <li><span class="label">P:</span>+255 612 839 274</li>
        <li><span class="label">E:</span>miriamholloway@postvale.example</li>
        <li><span class="label">W:</span>www.miriamholloway.example</li>
      </ul>
    </div>
  </section>

  <section class="card card-front" aria-label="Card front with company name">
    <div class="brand">
      <span class="brand-circle"></span>
      <span class="brand-name">Veritrace Kilonga</span>
    </div>
    <p class="tagline">Forensic Examinations<span class="dot">●</span>Employment Screening</p>
  </section>
</body>
</html>
```